GJ & DW Fencing Pty Ltd

We already have an existing logo created by Pixel Harbour however we have restructured to a company. We would like someone to add Pty Ltd to our business name please.

Colors

Designer to choose only greyscale colors for use in the design.

```html
<!DOCTYPE html>
<html lang="en">
<head>
<meta charset="utf-8">
<title>GJ &amp; DW Fencing Pty Ltd — Business Card</title>
<link rel="stylesheet" href="https://fonts.googleapis.com/css2?family=Merriweather:wght@700;900&family=Lato:wght@400&display=swap">
<style>
  :root {
    --backdrop: #d9d9d9;
    --card-dark: #0b0b0b;
    --card-light: #ffffff;
    --ink: #1a1a1a;
    --ink-soft: #2b2b2b;
    --rule: #b5b5b5;
    --paper: #f4f4f4;
  }
  * { box-sizing: border-box; margin: 0; padding: 0; }
  html, body {
    width: 1200px; height: 1015px; overflow: hidden;
    background: var(--backdrop);
  }
  .stage {
    width: 1200px; height: 1015px;
    display: flex; flex-direction: column; align-items: center; justify-content: center;
    gap: 56px;
  }
  .card {
    width: 700px; height: 400px;
    box-shadow: 0 10px 30px rgba(0,0,0,.25);
    position: relative;
  }
  .card--front {
    background: var(--card-dark);
    display: flex; align-items: center; justify-content: center;
  }
  .card--back {
    background: var(--card-light);
    display: flex; align-items: center;
    padding: 0 50px;
  }
  .wordmark {
    font-family: "Merriweather", Georgia, serif;
    font-weight: 900;
    text-transform: uppercase;
    line-height: 1.05;
    text-align: center;
    letter-spacing: .5px;
  }
  .wordmark__line--main { display: block; font-size: 44px; }
  .wordmark__line--sub { display: block; font-size: 26px; letter-spacing: 2px; }
  .card--front .wordmark { color: var(--paper); }
  .card--back .wordmark { color: var(--ink); }
  .brand { flex: 0 0 290px; display: flex; justify-content: center; }
  .card--back .wordmark__line--main { font-size: 36px; }
  .card--back .wordmark__line--sub { font-size: 21px; }
  .divider {
    width: 1px; height: 120px; background: var(--rule);
    margin: 0 30px 0 20px;
  }
  .contact { display: flex; flex-direction: column; gap: 9px; }
  .contact__name {
    font-family: "Merriweather", Georgia, serif;
    font-weight: 700; font-size: 17px; letter-spacing: .6px;
    text-transform: uppercase; color: var(--ink);
    margin-bottom: 4px;
  }
  .contact__row {
    display: flex; align-items: center; gap: 8px;
    font-family: "Lato", Arial, sans-serif; font-size: 17px; color: var(--ink-soft);
  }
  .contact__icon { width: 22px; height: 22px; flex: 0 0 22px; }
</style>
</head>
<body>
<main class="stage">
  <section class="card card--front" aria-label="Card front">
    <div class="wordmark">
      <span class="wordmark__line wordmark__line--main">GJ &amp; DW Fencing</span>
      <span class="wordmark__line wordmark__line--sub">Pty Ltd</span>
    </div>
  </section>

  <section class="card card--back" aria-label="Card back">
    <div class="brand">
      <div class="wordmark">
        <span class="wordmark__line wordmark__line--main">GJ &amp; DW Fencing</span>
        <span class="wordmark__line wordmark__line--sub">Pty Ltd</span>
      </div>
    </div>
    <div class="divider"></div>
    <div class="contact">
      <p class="contact__name">Tom Harland</p>
      <p class="contact__row">
        <svg class="contact__icon" viewBox="0 0 22 22" aria-hidden="true">
          <circle cx="11" cy="11" r="11" fill="#1a1a1a"/>
          <path d="M7.5 6h2l1 2.5-1.3 1a6 6 0 0 0 3.3 3.3l1-1.3 2.5 1v2a1 1 0 0 1-1 1A9 9 0 0 1 6.5 7a1 1 0 0 1 1-1z" fill="#fff"/>
        </svg>
        041 2555318
      </p>
      <p class="contact__row">
        <svg class="contact__icon" viewBox="0 0 22 22" aria-hidden="true">
          <circle cx="11" cy="11" r="11" fill="#1a1a1a"/>
          <rect x="5.5" y="7" width="11" height="8" fill="none" stroke="#fff" stroke-width="1.3"/>
          <path d="M5.5 7l5.5 4.5L16.5 7" fill="none" stroke="#fff" stroke-width="1.3"/>
        </svg>
        gjdwfencing@mailbox.com
      </p>
      <p class="contact__row">
        <svg class="contact__icon" viewBox="0 0 22 22" aria-hidden="true">
          <circle cx="11" cy="11" r="11" fill="#1a1a1a"/>
          <path d="M11 4.5a4.2 4.2 0 0 1 4.2 4.2c0 3.2-4.2 8.3-4.2 8.3S6.8 11.9 6.8 8.7A4.2 4.2 0 0 1 11 4.5z" fill="#fff"/>
          <circle cx="11" cy="8.7" r="1.6" fill="#1a1a1a"/>
        </svg>
        PO Box 418 Greyvale WA 6499
      </p>
    </div>
  </section>
</main>
</body>
</html>
```